Spring Exterior Painting Advertisement

Attached is the postcard that we used last year(file - pixelharbor_318939...vector....pdf.. The information contained will be the same except for it will be updated for use during the spring of 2023.

The second attachment (sept 2021mailer) is another design that we've used in the past.

```html
<!DOCTYPE html>
<html lang="en">
<head>
<meta charset="utf-8">
<title>Summit Painting – Spring Postcard</title>
<link rel="stylesheet" href="https://fonts.googleapis.com/css2?family=Montserrat:wght@400;500;600;700;800;900&display=swap">
<style>
:root{
  --stage:#d4d5d7;
  --paper:#ffffff;
  --berry:#a8375f;
  --berry-dark:#7b1f4a;
  --gold:#e5a823;
  --ocean:#1e6b98;
  --ink:#222222;
  --mint:#8fcfc0;
  --navy:#2a3a6e;
  --sky:#4fc1e0;
  --leaf:#3f8f3a;
  --flame:#e04a26;
  --orchid:#b24fa3;
}
*{box-sizing:border-box;margin:0;padding:0}
html,body{width:1200px;height:2688px;overflow:hidden}
body{background:var(--stage);font-family:"Montserrat",Arial,sans-serif;position:relative}
.postcard{position:absolute;left:50px;width:1100px;height:733px;background:var(--paper);overflow:hidden;box-shadow:0 6px 18px rgba(0,0,0,.18)}
.postcard--front{top:480px}
.postcard--back{top:1453px}

.brand{position:absolute;right:44px;display:flex;align-items:center;gap:8px;font-weight:800;font-size:22px;letter-spacing:.5px;color:var(--ink);white-space:nowrap}
.postcard--front .brand{top:126px}
.postcard--back .brand{top:112px}
.brand__mark{width:16px;height:16px;background:var(--ink)}

.paint-band{position:absolute;background:var(--berry);color:#fff;border-radius:6px;overflow:hidden}

/* front */
.offer{left:140px;top:50px;width:630px;height:180px;display:flex;align-items:center;padding-left:56px;white-space:nowrap}
.offer__lead{font-weight:900;font-size:40px;line-height:.92;text-transform:uppercase}
.offer__value{font-weight:900;font-size:112px;line-height:1;color:var(--gold);margin-left:14px;letter-spacing:-4px}
.offer__pct{font-weight:800;font-size:34px;color:var(--gold);align-self:flex-start;margin-top:38px}
.offer__code{margin-left:16px;text-align:center}
.offer__code-label{display:inline-block;background:#fff;color:var(--berry);font-weight:800;font-size:13px;padding:4px 10px;text-transform:uppercase}
.offer__code-value{display:block;font-weight:800;font-size:17px;margin-top:12px}

.hero-photo{position:absolute;left:0;top:240px;width:1100px;height:408px;background:linear-gradient(180deg,#f3f4f6 0%,#b8455f 28%,#2f4f8f 55%,#3f7d3a 88%,#6da84a 100%)}

.contact-bar{position:absolute;left:0;bottom:0;width:1100px;height:85px;background:var(--ocean);display:flex;align-items:center;padding-left:50px;color:#fff}
.contact{display:flex;align-items:center;gap:14px;white-space:nowrap}
.contact__phone{font-weight:800;font-size:44px}
.contact__web{font-weight:500;font-size:30px}
.contact-bar .contact__web{margin-left:88px}

/* back */
.sender{left:88px;top:44px;width:344px;height:116px;padding:18px 0 0 48px}
.sender__name{font-weight:800;font-size:24px;text-transform:uppercase}
.sender__line{font-size:18px;line-height:1.15}

.quote-title{position:absolute;left:55px;top:176px;font-weight:900;font-size:40px;line-height:1;color:var(--gold);text-transform:uppercase}
.quote-text{position:absolute;left:55px;top:268px;width:512px;font-size:13.5px;line-height:1.2;color:var(--ink);text-align:justify}

.services{position:absolute;left:50px;top:344px;width:516px;height:237px;background:var(--ocean);border-radius:4px;display:grid;grid-template-columns:1fr 1.15fr;grid-auto-rows:1fr;padding:22px 20px;gap:10px 10px;color:#fff;list-style:none}
.service{display:flex;align-items:center;gap:14px;font-size:19px;line-height:1.05}
.service__icon{flex:none;width:28px;height:28px;border:2px solid var(--gold);border-radius:50%}

.compare{position:absolute;left:0;top:0}
.compare__label{position:absolute;top:330px;width:78px;height:18px;border-radius:9px;background:var(--berry-dark);color:#fff;font-size:11px;font-weight:600;text-align:center;line-height:18px}
.compare__photo{position:absolute;top:353px;width:244px;height:244px;border-radius:50%}
.compare__photo--before{left:612px;background:radial-gradient(circle at 45% 45%,#f4f4f4,#c9c9c9)}
.compare__photo--after{left:800px;background:radial-gradient(circle at 55% 45%,#a6e0d2,#5dbba7)}

.contact-row{position:absolute;left:50px;top:618px;width:1000px;display:flex;align-items:center;justify-content:space-between;color:var(--ocean)}

.swatches{position:absolute;left:50px;top:703px;width:994px;height:7px;display:flex;gap:6px}
.swatches span{flex:1}
</style>
</head>
<body>

<section class="postcard postcard--front" aria-label="Postcard front">
  <div class="paint-band offer">
    <div class="offer__lead">Spring<br>Save</div>
    <div class="offer__value">15</div>
    <div class="offer__pct">%</div>
    <div class="offer__code">
      <span class="offer__code-label">Coupon code</span>
      <span class="offer__code-value">“SPRINGEXT2023”</span>
    </div>
  </div>
  <div class="brand"><span class="brand__mark"></span>SUMMIT PAINTING</div>
  <div class="hero-photo" role="img" aria-label="Photo of a blue two-storey house with a red roof, white garage doors and green shrubs"></div>
  <div class="contact-bar">
    <div class="contact">
      <svg width="26" height="26" viewBox="0 0 24 24" fill="none" stroke="#e5a823" stroke-width="2"><path d="M5 3h4l2 5-3 2a12 12 0 0 0 6 6l2-3 5 2v4a2 2 0 0 1-2 2A18 18 0 0 1 3 5a2 2 0 0 1 2-2z"/></svg>
      <span class="contact__phone">(555) 014-2290</span>
    </div>
    <div class="contact contact__web">
      <svg width="26" height="26" viewBox="0 0 24 24" fill="none" stroke="#e5a823" stroke-width="2"><circle cx="12" cy="12" r="9"/><path d="M3 12h18M12 3c3 3 3 15 0 18M12 3c-3 3-3 15 0 18"/></svg>
      <span>SUMMITPAINTINGCO.COM</span>
    </div>
  </div>
</section>

<section class="postcard postcard--back" aria-label="Postcard back">
  <div class="paint-band sender">
    <div class="sender__name">Summit Painting</div>
    <div class="sender__line">48 Harbor Way Unit B</div>
    <div class="sender__line">Lakeview, WI 53990</div>
  </div>
  <div class="brand"><span class="brand__mark"></span>SUMMIT PAINTING</div>

  <h1 class="quote-title">Request your<br>free Summit quote</h1>
  <p class="quote-text">Summit Painting's local team offers professional painting for your home's exterior and interior surfaces. With over 19 years in business, we offer skillful workmanship backed by a three-year warranty.</p>

  <ul class="services">
    <li class="service"><span class="service__icon"></span>Pressure<br>Washing</li>
    <li class="service"><span class="service__icon"></span>Exterior Painting<br>&amp; staining</li>
    <li class="service"><span class="service__icon"></span>Interior<br>Painting</li>
    <li class="service"><span class="service__icon"></span>Cabinetry<br>finishing</li>
    <li class="service"><span class="service__icon"></span>Carpentry</li>
    <li class="service"><span class="service__icon"></span>Color<br>Consultations</li>
  </ul>

  <div class="compare">
    <span class="compare__label" style="left:695px">Before</span>
    <span class="compare__label" style="left:883px">After</span>
    <div class="compare__photo compare__photo--before" role="img" aria-label="Before photo: bare white room with a ladder"></div>
    <div class="compare__photo compare__photo--after" role="img" aria-label="After photo: the same room painted mint green"></div>
  </div>

  <div class="contact-row">
    <div class="contact">
      <svg width="26" height="26" viewBox="0 0 24 24" fill="none" stroke="#e5a823" stroke-width="2"><path d="M5 3h4l2 5-3 2a12 12 0 0 0 6 6l2-3 5 2v4a2 2 0 0 1-2 2A18 18 0 0 1 3 5a2 2 0 0 1 2-2z"/></svg>
      <span class="contact__phone">(555) 014-2290</span>
    </div>
    <div class="contact contact__web">
      <svg width="26" height="26" viewBox="0 0 24 24" fill="none" stroke="#e5a823" stroke-width="2"><circle cx="12" cy="12" r="9"/><path d="M3 12h18M12 3c3 3 3 15 0 18M12 3c-3 3-3 15 0 18"/></svg>
      <span>SUMMITPAINTINGCO.COM</span>
    </div>
  </div>

  <div class="swatches" aria-hidden="true">
    <span style="background:var(--berry-dark)"></span>
    <span style="background:var(--gold)"></span>
    <span style="background:var(--mint)"></span>
    <span style="background:var(--navy)"></span>
    <span style="background:var(--sky)"></span>
    <span style="background:var(--ocean)"></span>
    <span style="background:var(--leaf)"></span>
    <span style="background:var(--flame)"></span>
    <span style="background:var(--gold)"></span>
    <span style="background:var(--orchid)"></span>
  </div>
</section>

</body>
</html>
```